furniture and home contents restoration

I need to list the services that we perform in our studio.
we serve the general public as well as the insurance/ remediation industry

```html
<!DOCTYPE html>
<html lang="en">
<head>
<meta charset="utf-8">
<title>Ashgrove Studios — Business Card</title>
<link href="https://fonts.googleapis.com/css2?family=PT+Serif:wght@400;700&display=swap" rel="stylesheet">
<style>
:root{
  --ink:#21303a;
  --paper:#ffffff;
  --backdrop:#d9d9d9;
}
*{margin:0;padding:0;box-sizing:border-box}
html,body{width:1200px;height:965px;overflow:hidden;background:var(--backdrop)}
body{position:relative;font-family:"PT Serif",Georgia,serif;color:var(--ink)}
.card{position:absolute;top:159px;width:383px;height:669px}
.card-front{left:186px;background:var(--paper)}
.card-back{left:653px;background:var(--ink);color:var(--paper)}
.abs{position:absolute;left:0;right:0;text-align:center}
.brand{font-weight:700;letter-spacing:.3px}
.card-front .brand{top:48px;font-size:48px;line-height:51px}
.card-back .brand{top:24px;font-size:51px;line-height:53px}
.name-band{position:absolute;left:0;right:0;top:278px;height:42px;background:var(--ink);color:var(--paper);
  font-weight:700;font-size:27px;line-height:44px;text-align:center;letter-spacing:.3px}
.contact-icons{position:absolute;left:34px;top:353px}
.contact-lines{top:390px;font-size:17px;line-height:22.8px}
.rule{position:absolute;height:2px;background:var(--ink)}
.card-front .rule{left:45px;width:294px;top:521px}
.tagline{top:540px;font-size:17px;line-height:23px}
.specialty{top:616px;font-size:18px;text-transform:uppercase}
.services{position:absolute;left:34px;list-style:none;font-size:14px;line-height:17.8px;text-transform:uppercase;white-space:nowrap}
.services li::before{content:"";display:inline-block;width:5px;height:5px;border-radius:50%;background:var(--paper);margin-right:4px;vertical-align:2px}
.services-a{top:170px}
.services-b{top:377px}
.card-back .rule{left:34px;width:314px;top:572px;background:var(--paper)}
.consulting{position:absolute;left:34px;top:592px;font-size:12.3px;line-height:16px;text-transform:uppercase}
</style>
</head>
<body>
<section class="card card-front">
  <h1 class="abs brand">ASHGROVE<br>STUDIOS</h1>
  <div class="name-band">DANIEL MORETTI</div>
  <svg class="contact-icons" width="315" height="24" viewBox="0 0 315 24" aria-hidden="true">
    <path d="M0 12 Q40 10 78 11 L78 12.5 Q40 13 0 12Z" fill="var(--ink)"/>
    <path d="M315 12 Q275 10 237 11 L237 12.5 Q275 13 315 12Z" fill="var(--ink)"/>
    <g fill="var(--ink)">
      <rect x="91" y="2" width="20" height="20"/><rect x="119" y="2" width="20" height="20"/>
      <rect x="147" y="2" width="20" height="20"/><rect x="175" y="2" width="20" height="20"/>
      <rect x="203" y="2" width="20" height="20"/>
    </g>
    <g fill="none" stroke="#fff" stroke-width="1.3">
      <path d="M96 6 Q95 13 104 19 L106 17 L103 14 L101 15 Q99 12 99 10 L100 9 L98 6Z"/>
      <rect x="125" y="5" width="8" height="14" rx="1"/>
      <rect x="151" y="9" width="12" height="7"/><rect x="154" y="6" width="6" height="3"/><rect x="154" y="14" width="6" height="4"/>
      <rect x="179" y="7" width="12" height="9"/><path d="M179 7 L185 12 L191 7"/>
      <path d="M213 19 Q207 12 207 10 A6 6 0 0 1 219 10 Q219 12 213 19Z"/><circle cx="213" cy="10" r="2"/>
    </g>
  </svg>
  <p class="abs contact-lines">555 010 2718<br>555 010 5942<br>555 010 8163<br>info@ashgrovestudios.com<br>12 mill brook rd. easton, ny 10500</p>
  <div class="rule"></div>
  <p class="abs tagline">serving the general public and the<br>insurance industry for over 40 years</p>
  <p class="abs specialty">Home Contents Restoration</p>
</section>

<section class="card card-back">
  <h2 class="abs brand">ASHGROVE<br>STUDIOS</h2>
  <ul class="services services-a">
    <li>Antique repair and restoration</li>
    <li>Art cleaning and remounting</li>
    <li>Art and mirror frame repair</li>
    <li>Chandelier cleaning and restoration</li>
    <li>Document restoration</li>
    <li>Glass, ceramic, and mirror repair</li>
    <li>Hardware repair and restoration</li>
    <li>Kitchen removal and reinstallation</li>
    <li>Lamp cleaning and restoration</li>
    <li>Lamp shade replacement</li>
  </ul>
  <ul class="services services-b">
    <li>Metal polishing and restoration</li>
    <li>Odor removal and ozone services</li>
    <li>Photo restoration</li>
    <li>Upholstery cleaning and deodorizing</li>
    <li>In-house upholstery and reupholstery</li>
    <li>Rug cleaning and restoration</li>
    <li>Musical instrument restoration</li>
    <li>Window treatment repair/ restoration</li>
    <li>Leather restoration and replacement</li>
    <li>Piano restoration and repair</li>
  </ul>
  <div class="rule"></div>
  <p class="consulting">On-site inspections and desk review services<br>Assessment reports and estimates for repair<br>and restoration</p>
</section>
</body>
</html>
```